Spring Detox sale graphics for social media

You MUST read the Brief in the WORD document and follow the instructions there. I want to create 10 social media graphics (new Instagram size 4:5 (1080 x 1350 pixels) focusing on our Mother’s Day Spring Detox Sale graphics, using any of the pics attached. Use the attached pics, NO RANDOM STOCK PHOTOGRAPHY. For the color scheme of the graphics, they should all be complementary to the product colors or feel like Spring time.

Target Market(s)

primarily women

Requirements
Must have
• the photos and text attached

```html
<!DOCTYPE html>
<html lang="en">
<head>
<meta charset="utf-8">
<title>Mother's Day Spring Detox Sale – Social Set</title>
<link href="https://fonts.googleapis.com/css2?family=Anton&family=Archivo+Black&family=Oswald:wght@500;600&family=Playfair+Display:ital,wght@0,900;1,700;1,900&family=Plus+Jakarta+Sans:wght@600;700&display=swap" rel="stylesheet">
<style>
:root{
  --page:#ffffff;
  --blush:#fde7f3;
  --blush-deep:#f8cfe5;
  --rose:#c0518f;
  --hot:#d960a3;
  --light-rose:#f2a9d0;
  --plum:#82295a;
  --plum-dark:#6e1f4b;
  --white:#ffffff;
}
*{margin:0;padding:0;box-sizing:border-box}
html,body{width:1200px;height:608px;overflow:hidden;background:var(--page)}
.board{position:relative;width:1200px;height:608px}
.tile{position:absolute;width:225px;height:281px;overflow:hidden;
  background:radial-gradient(ellipse at 50% 35%,var(--blush) 0%,var(--blush-deep) 100%);
  text-align:center;color:var(--rose)}
.r1{top:19px}.r2{top:308px}
.c1{left:22px}.c2{left:255px}.c3{left:488px}.c4{left:720px}.c5{left:953px}

.abs{position:absolute;left:0;right:0;white-space:nowrap}
.script{font-family:"Playfair Display",serif;font-style:italic;font-weight:900;letter-spacing:-1px;line-height:1.1}
.serif-cap{font-family:"Playfair Display",serif;font-weight:900;letter-spacing:-4px;line-height:.8}
.block{font-family:"Archivo Black",sans-serif;line-height:.85}
.cond{font-family:"Oswald",sans-serif;font-weight:600;line-height:1}
.slant{font-family:"Anton",sans-serif;transform:skewX(-10deg);line-height:1;letter-spacing:-.5px}
.sans{font-family:"Plus Jakarta Sans",sans-serif;font-weight:700}
.highlight{display:inline-block;background:linear-gradient(transparent 40%,var(--light-rose) 40%,var(--light-rose) 85%,transparent 85%);padding:0 4px}

.arch{position:absolute;left:0;top:0;width:225px;height:281px}
.photo{position:absolute;left:50px;top:94px;width:126px;height:118px;border-radius:6px;
  background:linear-gradient(180deg,#3a2a2a 0%,#f1ecef 30%,#f5f2f4 55%,#2a2226 75%,#e8e6ea 100%)}
.ghost{position:absolute;top:105px;width:32px;height:55px;border-radius:8px;background:#ece7ec;opacity:.7}

.ribbon{position:absolute;left:20px;width:186px;background:var(--plum);color:var(--white);z-index:1;
  clip-path:polygon(3% 0,97% 0,100% 100%,0 100%);display:flex;flex-direction:column;justify-content:center;align-items:center}
.ribbon-label{position:absolute;left:50%;transform:translateX(-50%);z-index:2;background:var(--plum);color:var(--white);
  font-size:10px;padding:1px 5px;line-height:1.2;white-space:nowrap}
.tag{position:absolute;left:0;right:0;color:var(--plum)}
.bottle{position:absolute;width:20px;height:34px;border-radius:5px}
</style>
</head>
<body>
<main class="board">

<!-- 1 -->
<section class="tile r1 c1">
  <svg class="arch" viewBox="0 0 225 281"><path d="M45 230 V180 A67 67 0 0 1 179 180 V230Z" fill="var(--rose)"/></svg>
  <div class="ghost" style="left:18px"></div><div class="ghost" style="left:178px;top:60px"></div>
  <div class="photo" role="img" aria-label="Smiling woman in a white knit top behind a row of supplement bottles"></div>
  <div class="abs cond" style="top:14px;font-size:19px;font-weight:500;transform:skewX(-8deg)">Mother’s Day</div>
  <div class="abs serif-cap" style="top:42px;font-size:60px">SPRING</div>
  <div class="ribbon sans" style="top:224px;height:38px;font-size:12.5px;line-height:1.2">DETOX SALE<br>25% Off Everything!</div>
</section>

<!-- 2 -->
<section class="tile r1 c2">
  <svg class="arch" viewBox="0 0 225 281"><path d="M45 235 V180 A67 67 0 0 1 179 180 V235Z" fill="var(--plum)"/><path d="M58 230 V180 A55 55 0 0 1 168 180 V230Z" fill="var(--light-rose)" opacity=".7"/></svg>
  <div class="ghost" style="left:18px"></div><div class="ghost" style="left:178px;top:60px"></div>
  <div class="photo" role="img" aria-label="Smiling woman in a white knit top behind a row of supplement bottles"></div>
  <div class="abs block" style="top:14px;font-size:38px">25% Off</div>
  <div class="abs script" style="top:50px;font-size:31px;color:var(--plum)"><span class="highlight">Mother’s Day</span></div>
  <div class="ribbon block" style="top:228px;height:36px;font-size:30px;letter-spacing:5px">SALE</div>
  <div class="ribbon-label sans" style="top:215px">SPRING DETOX</div>
</section>

<!-- 3 -->
<section class="tile r1 c3">
  <svg class="arch" viewBox="0 0 225 281"><path d="M45 235 V180 A67 67 0 0 1 179 180 V235Z" fill="var(--rose)"/></svg>
  <div class="ghost" style="left:18px"></div><div class="ghost" style="left:178px;top:60px"></div>
  <div class="photo" role="img" aria-label="Smiling woman in a white knit top behind a row of supplement bottles"></div>
  <div class="abs block" style="top:14px;font-size:38px">25% Off</div>
  <div class="abs script" style="top:53px;font-size:26px;color:var(--plum)"><span class="highlight">All Supplements</span></div>
  <div class="ribbon cond" style="top:226px;height:38px;font-size:23px;letter-spacing:-.5px">SPRING DETOX SALE</div>
</section>

<!-- 4 -->
<section class="tile r1 c4">
  <svg class="arch" viewBox="0 0 225 281"><path d="M45 230 V180 A67 67 0 0 1 179 180 V230Z" fill="var(--plum)"/><path d="M52 230 V180 A60 60 0 0 1 172 180 V230Z" fill="var(--hot)"/></svg>
  <div class="ghost" style="left:18px"></div><div class="ghost" style="left:178px;top:60px"></div>
  <div class="photo" role="img" aria-label="Smiling woman in a white knit top behind a row of supplement bottles"></div>
  <div class="abs block" style="top:17px;font-size:24px;color:var(--plum-dark)">25% Off</div>
  <div class="abs serif-cap" style="top:44px;font-size:60px">SPRING</div>
  <div class="ribbon cond" style="top:214px;height:40px;font-size:32px;font-weight:500;letter-spacing:-1px">DETOX SALE</div>
  <div class="tag sans" style="top:261px;font-size:11.5px">Spring Reset. Summer Ready.</div>
</section>

<!-- 5 -->
<section class="tile r1 c5">
  <svg class="arch" viewBox="0 0 225 281"><path d="M45 225 V180 A67 67 0 0 1 179 180 V225Z" fill="var(--rose)"/><path d="M52 225 V180 A60 60 0 0 1 172 180 V225Z" fill="var(--light-rose)"/></svg>
  <div class="ghost" style="left:18px"></div><div class="ghost" style="left:178px;top:60px"></div>
  <div class="photo" role="img" aria-label="Smiling woman in a white knit top behind a row of supplement bottles"></div>
  <div class="abs block" style="top:14px;font-size:38px">25% Off</div>
  <div class="abs script" style="top:46px;font-size:38px;color:var(--plum-dark)">Everything</div>
  <div class="ribbon cond" style="top:206px;height:38px;font-size:30px;font-weight:500;letter-spacing:-1px">MOTHER’S DAY</div>
  <div class="tag sans" style="top:250px;font-size:16px">Spring Detox Sale</div>
</section>

<!-- 6 -->
<section class="tile r2 c1">
  <svg class="arch" viewBox="0 0 225 281"><path d="M45 230 V180 A67 67 0 0 1 179 180 V230Z" fill="var(--plum)"/><path d="M52 230 V180 A60 60 0 0 1 172 180 V230Z" fill="var(--light-rose)"/></svg>
  <div class="ghost" style="left:18px"></div><div class="ghost" style="left:178px;top:60px"></div>
  <div class="photo" role="img" aria-label="Smiling woman in a white knit top behind a row of supplement bottles"></div>
  <div class="abs block" style="top:14px;font-size:38px">25% Off</div>
  <div class="abs script" style="top:50px;font-size:31px;color:var(--plum)"><span class="highlight">Mother’s Day</span></div>
  <div class="ribbon block" style="top:214px;height:38px;font-size:30px;letter-spacing:5px">SALE</div>
  <div class="tag sans" style="top:257px;font-size:13.5px">Feel Amazing Again</div>
</section>

<!-- 7 -->
<section class="tile r2 c2">
  <div class="abs block" style="top:18px;left:18px;right:auto;font-size:100px;letter-spacing:-6px">25</div>
  <div class="abs block" style="top:18px;left:150px;right:auto;font-size:58px">%</div>
  <div class="abs block" style="top:74px;left:150px;right:auto;font-size:25px">OFF</div>
  <div class="abs block" style="top:104px;font-size:17px;color:var(--plum-dark)">MOTHER’S DAY SALE</div>
  <div class="abs block" style="top:123px;font-size:35px;letter-spacing:-1px">REFRESH</div>
  <div class="abs block" style="top:156px;font-size:29px;letter-spacing:-1px;color:var(--plum-dark)">YOUR BODY</div>
  <div role="img" aria-label="Four supplement bottles in a row" style="position:absolute;left:18px;top:192px;width:190px;height:82px;border-radius:8px;background:linear-gradient(90deg,#f4eef2,#fff 25%,#f7e3e6 50%,#fff 75%,#e8eaf4)"></div>
</section>

<!-- 8 -->
<section class="tile r2 c3">
  <div class="abs block" style="top:18px;left:18px;right:auto;font-size:100px;letter-spacing:-6px;color:var(--hot)">25</div>
  <div class="abs block" style="top:18px;left:150px;right:auto;font-size:58px;color:var(--hot)">%</div>
  <div class="abs block" style="top:74px;left:150px;right:auto;font-size:25px;color:var(--hot)">OFF</div>
  <div class="abs slant" style="top:100px;font-size:58px;color:var(--plum)">SPRING</div>
  <div style="position:absolute;left:16px;top:164px;width:193px;height:34px;background:var(--rose)"></div>
  <div class="abs script" style="top:163px;font-size:32px;color:var(--white)">Detox Sale</div>
  <div class="abs slant" style="top:202px;font-size:20px;color:var(--plum)">THIS SPRING SHINE LIKE</div>
  <div class="abs block" style="top:228px;font-size:38px;color:var(--rose)">SUMMER</div>
</section>

<!-- 9 -->
<section class="tile r2 c4">
  <div class="abs block" style="top:18px;left:18px;right:auto;font-size:100px;letter-spacing:-6px;color:var(--plum)">25</div>
  <div class="abs block" style="top:18px;left:150px;right:auto;font-size:58px;color:var(--plum)">%</div>
  <div class="abs block" style="top:74px;left:150px;right:auto;font-size:25px;color:var(--hot)">OFF</div>
  <div class="abs slant" style="top:104px;font-size:31px;color:var(--hot)">MOTHER’S DAY</div>
  <div class="block" style="position:absolute;left:16px;top:143px;width:195px;height:58px;background:var(--plum);color:var(--white);font-size:54px;line-height:60px">SALE</div>
  <div class="abs slant" style="top:208px;font-size:24px;letter-spacing:-1px;color:var(--rose)">Detox this SUMMER</div>
  <div class="abs slant" style="top:237px;font-size:24px;letter-spacing:-1px;color:var(--plum)">Shine this SUMMER</div>
</section>

<!-- 10 -->
<section class="tile r2 c5">
  <div class="abs block" style="top:22px;left:18px;right:auto;font-size:100px;letter-spacing:-6px">25</div>
  <div class="abs block" style="top:22px;left:150px;right:auto;font-size:58px">%</div>
  <div class="abs block" style="top:78px;left:150px;right:auto;font-size:25px">OFF</div>
  <div class="abs slant" style="top:110px;font-size:23px;color:var(--plum)">MOTHER’S DAY SALE</div>
  <div class="abs serif-cap" style="top:140px;font-size:48px;letter-spacing:-3px">SPRING</div>
  <div class="bottle" role="img" aria-label="Supplement bottle" style="left:10px;top:185px;background:linear-gradient(#fff,#e6ecea)"></div>
  <div class="bottle" role="img" aria-label="Supplement bottle" style="left:195px;top:185px;background:linear-gradient(#fff,#f0e2ec)"></div>
  <div class="abs slant" style="top:187px;font-size:27px;color:var(--hot)">DETOX FOR A</div>
  <div class="abs slant" style="top:222px;font-size:33px;color:var(--rose)">SUMMER BODY</div>
</section>

</main>
</body>
</html>
```